Company identity deisgn should support 2 languages

I would like to get our company identity design
This includes the following only
Business Cards 2 languages Arabic and English
Email signature
Letterhead
Linkedin profile images
Attached is the logo in Ai format

Requirements
Must have
• For business card
Must have
Name and Adrees in arabic
Name and Address in english
You might use both side of the card
Should not have
• Any pictures other than the logo

```html
<!DOCTYPE html>
<html lang="en">
<head>
<meta charset="utf-8">
<title>Northvane Systems – Stationery</title>
<link href="https://fonts.googleapis.com/css2?family=Open+Sans:wght@400;600;700&family=Roboto+Condensed:wght@400;700&family=Cairo:wght@400;600&display=swap" rel="stylesheet">
<style>
  :root{
    --brand-blue:#1469b3;
    --ink:#4a4d52;
    --ink-soft:#6b6f75;
    --paper:#ffffff;
    --paper-cool:#f7f7f9;
    --stage-top:#ebe9e7;
    --stage-bottom:#e1e2e4;
    --faint-mark:#e6e8f2;
    --sans:'Open Sans', Arial, sans-serif;
    --cond:'Roboto Condensed', 'Arial Narrow', sans-serif;
    --arabic:'Cairo', 'Open Sans', sans-serif;
  }
  *{box-sizing:border-box;margin:0;padding:0}
  html,body{width:1200px;height:2195px;overflow:hidden}
  body{position:relative;font-family:var(--sans);color:var(--ink);background:var(--stage-bottom)}
  .stage-cards{position:absolute;left:0;top:0;width:1200px;height:960px;background:var(--stage-top)}
  .card{position:absolute;width:560px;height:320px;box-shadow:0 14px 28px rgba(0,0,0,.14)}
  .card-back{left:90px;top:110px;background:var(--brand-blue);color:#fff}
  .card-front{left:560px;top:480px;background:var(--paper)}
  .brand{display:flex;align-items:center;gap:12px}
  .brand-dot{width:30px;height:30px;border-radius:50%;flex:none}
  .brand-name{font-family:var(--sans);font-weight:600;letter-spacing:.08em;text-transform:uppercase}
  .card-back .brand{position:absolute;left:150px;top:120px}
  .card-back .brand-dot{background:#fff}
  .card-back .brand-name{font-size:24px;color:#fff}
  .card-back .web{position:absolute;left:210px;top:232px;font-size:15px;letter-spacing:.06em}
  .card-front .brand{position:absolute;left:40px;top:36px}
  .card-front .brand-dot{background:var(--brand-blue)}
  .card-front .brand-name{font-size:20px;color:var(--brand-blue)}
  .person-name{font-family:var(--sans);font-weight:700;color:var(--brand-blue);font-size:19px}
  .person-name .ar{font-family:var(--arabic);font-weight:600}
  .person-title{font-weight:600;font-size:13px;color:var(--ink)}
  .card-front .person{position:absolute;left:40px;top:112px}
  .card-front .address{position:absolute;left:40px;top:178px;font-size:13px;line-height:1.5}
  .card-front .address .ar{font-family:var(--arabic);direction:rtl;text-align:left;unicode-bidi:plaintext}
  .card-front .contacts{position:absolute;right:32px;top:178px;font-size:13px;line-height:1.55}
  .accent-bar{position:absolute;left:0;width:14px;height:30px;background:var(--brand-blue)}
  .card-front .accent-bar{top:190px}
  .contacts li{list-style:none;display:flex;align-items:center;gap:6px}
  .icon{width:13px;height:13px;fill:var(--brand-blue);flex:none}

  .letterhead{position:absolute;top:1082px;width:417px;height:581px;background:linear-gradient(180deg,var(--paper) 0%,var(--paper-cool) 100%);box-shadow:0 8px 16px rgba(0,0,0,.12);overflow:hidden}
  .letterhead.lh-1{left:166px}
  .letterhead.lh-2{left:620px}
  .letterhead .brand{position:absolute;left:38px;top:52px;gap:7px}
  .letterhead .brand-dot{width:16px;height:16px;background:var(--brand-blue)}
  .letterhead .brand-name{font-size:9px;color:var(--brand-blue)}
  .lh-contacts{position:absolute;left:274px;top:36px;font-size:8px;line-height:1.35;color:var(--ink)}
  .lh-contacts li{list-style:none;display:flex;align-items:center;gap:3px}
  .lh-contacts .icon{width:7px;height:7px}
  .lh-body{position:absolute;left:38px;top:140px;width:342px;font-size:6.6px;line-height:1.66;color:var(--ink-soft);text-align:justify}
  .lh-body p{margin-bottom:11px}
  .lh-signature{position:absolute;left:38px;top:404px;width:52px;height:44px;background:#d9dadd;border-radius:4px}
  .lh-mark{position:absolute;right:-40px;bottom:-60px;width:200px;height:200px;border-radius:50%;background:var(--faint-mark);opacity:.6}
  .lh-footer{position:absolute;left:38px;top:528px;font-family:var(--arabic);font-size:8px;line-height:1.55;color:var(--ink);unicode-bidi:plaintext}
  .letterhead .accent-bar{top:527px;width:10px;height:22px}

  .email-signature{position:absolute;left:212px;top:1842px;width:790px;height:317px;background:var(--paper);box-shadow:6px 8px 12px rgba(0,0,0,.25);overflow:hidden;font-family:var(--cond)}
  .sig-mark{position:absolute;right:20px;top:-10px;width:250px;height:250px;border-radius:50%;background:var(--faint-mark);opacity:.7}
  .sig-name{position:absolute;left:52px;top:50px;font-size:29px;font-weight:700;color:var(--brand-blue)}
  .sig-name .ar{font-family:var(--arabic);font-weight:400}
  .sig-title{position:absolute;left:52px;top:88px;font-size:21px;color:var(--ink)}
  .sig-address-ar{position:absolute;left:52px;top:128px;font-family:var(--arabic);font-size:19px;line-height:1.6;color:var(--ink);unicode-bidi:plaintext}
  .sig-contacts{position:absolute;left:52px;top:194px;font-size:21px;line-height:1.38;color:var(--ink)}
  .sig-contacts li{list-style:none;display:flex;align-items:center;gap:6px}
  .sig-contacts .icon{width:17px;height:17px}
  .sig-address-en{position:absolute;right:52px;top:238px;font-size:21px;line-height:1.3;text-align:right;color:var(--ink)}
</style>
</head>
<body>

<section class="stage-cards">
  <article class="card card-back">
    <div class="brand"><span class="brand-dot"></span><span class="brand-name">Northvane Systems</span></div>
    <p class="web">www.northvaneweb.com</p>
  </article>

  <article class="card card-front">
    <div class="brand"><span class="brand-dot"></span><span class="brand-name">Northvane Systems</span></div>
    <div class="person">
      <p class="person-name">KARIM DALTON <span class="ar">(كريم دالتون)</span></p>
      <p class="person-title">Managing Director</p>
    </div>
    <span class="accent-bar"></span>
    <div class="address">
      <p>42 Cedar Ridge Way, Vernon</p>
      <p>B.C. Canada V1T 5K8</p>
      <p class="ar">42 طريق سيدار ريدج، فيرنون</p>
      <p class="ar">كولومبيا البريطانية كندا V1T 5K8</p>
    </div>
    <ul class="contacts">
      <li><svg class="icon" viewBox="0 0 16 16"><path d="M3 1h3l1.5 4-2 1.3a9 9 0 0 0 4.2 4.2L11 8.5l4 1.5v3a2 2 0 0 1-2 2A13 13 0 0 1 1 3a2 2 0 0 1 2-2z"/></svg>555.214.7720</li>
      <li><svg class="icon" viewBox="0 0 16 16"><path d="M1 3h14v10H1z M1 3l7 6 7-6" stroke="#fff" stroke-width="1.2"/></svg>info@northvanemail.com</li>
      <li><svg class="icon" viewBox="0 0 16 16"><circle cx="8" cy="8" r="7"/></svg>www.northvaneweb.com</li>
    </ul>
  </article>
</section>

<article class="letterhead lh-1">
  <div class="brand"><span class="brand-dot"></span><span class="brand-name">Northvane Systems</span></div>
  <ul class="lh-contacts">
    <li>42 Cedar Ridge Way, Vernon</li>
    <li>B.C. Canada V1T 5K8</li>
    <li><svg class="icon" viewBox="0 0 16 16"><path d="M3 1h3l1.5 4-2 1.3a9 9 0 0 0 4.2 4.2L11 8.5l4 1.5v3a2 2 0 0 1-2 2A13 13 0 0 1 1 3a2 2 0 0 1 2-2z"/></svg>555.214.7720</li>
    <li><svg class="icon" viewBox="0 0 16 16"><path d="M1 3h14v10H1z"/></svg>info@northvanemail.com</li>
    <li><svg class="icon" viewBox="0 0 16 16"><circle cx="8" cy="8" r="7"/></svg>www.northvaneweb.com</li>
  </ul>
  <div class="lh-body">
    <p>Dear customer,</p>
    <p>Lorem ipsum dolor sit amet, consectetur adipisicing elit, sed do eiusmod tempor incididunt ut labore et dolore magna aliqua. Ut enim ad minim veniam, quis nostrud exercitation ullamco laboris nisi ut aliquip ex ea commodo consequat. Duis aute irure dolor in reprehenderit in voluptate velit esse cillum dolore eu fugiat nulla pariatur. Excepteur sint occaecat cupidatat non proident, sunt in culpa qui officia deserunt mollit anim id est laborum.</p>
    <p>Lorem ipsum dolor sit amet, consectetur adipisicing elit, sed do eiusmod tempor incididunt ut labore et dolore magna aliqua. Ut enim ad minim veniam, quis nostrud exercitation ullamco laboris nisi ut aliquip ex ea commodo consequat. Duis aute irure dolor in reprehenderit in voluptate velit esse cillum dolore eu fugiat nulla pariatur. Excepteur sint occaecat cupidatat non proident, sunt in culpa qui officia deserunt mollit anim id est laborum.</p>
    <p>Lorem ipsum dolor sit amet, consectetur adipisicing elit, sed do eiusmod tempor incididunt ut labore et dolore magna aliqua. Ut enim ad minim veniam, quis nostrud exercitation ullamco laboris nisi ut aliquip ex ea commodo consequat. Duis aute irure dolor in reprehenderit in voluptate velit esse cillum dolore eu fugiat nulla pariatur. Excepteur sint occaecat cupidatat non proident, sunt in culpa qui officia deserunt mollit anim id est laborum.</p>
    <p>Yours Sincerely,</p>
  </div>
  <div class="lh-signature" role="img" aria-label="Handwritten signature"></div>
  <span class="lh-mark"></span>
  <span class="accent-bar"></span>
  <div class="lh-footer"><p>42 طريق سيدار ريدج، فيرنون</p><p>كولومبيا البريطانية كندا V1T 5K8</p></div>
</article>

<article class="letterhead lh-2">
  <div class="brand"><span class="brand-dot"></span><span class="brand-name">Northvane Systems</span></div>
  <ul class="lh-contacts">
    <li>42 Cedar Ridge Way, Vernon</li>
    <li>B.C. Canada V1T 5K8</li>
    <li><svg class="icon" viewBox="0 0 16 16"><path d="M3 1h3l1.5 4-2 1.3a9 9 0 0 0 4.2 4.2L11 8.5l4 1.5v3a2 2 0 0 1-2 2A13 13 0 0 1 1 3a2 2 0 0 1 2-2z"/></svg>555.214.7720</li>
    <li><svg class="icon" viewBox="0 0 16 16"><path d="M1 3h14v10H1z"/></svg>info@northvanemail.com</li>
    <li><svg class="icon" viewBox="0 0 16 16"><circle cx="8" cy="8" r="7"/></svg>www.northvaneweb.com</li>
  </ul>
  <div class="lh-body">
    <p>Dear customer,</p>
    <p>Lorem ipsum dolor sit amet, consectetur adipisicing elit, sed do eiusmod tempor incididunt ut labore et dolore magna aliqua. Ut enim ad minim veniam, quis nostrud exercitation ullamco laboris nisi ut aliquip ex ea commodo consequat. Duis aute irure dolor in reprehenderit in voluptate velit esse cillum dolore eu fugiat nulla pariatur. Excepteur sint occaecat cupidatat non proident, sunt in culpa qui officia deserunt mollit anim id est laborum.</p>
    <p>Lorem ipsum dolor sit amet, consectetur adipisicing elit, sed do eiusmod tempor incididunt ut labore et dolore magna aliqua. Ut enim ad minim veniam, quis nostrud exercitation ullamco laboris nisi ut aliquip ex ea commodo consequat. Duis aute irure dolor in reprehenderit in voluptate velit esse cillum dolore eu fugiat nulla pariatur. Excepteur sint occaecat cupidatat non proident, sunt in culpa qui officia deserunt mollit anim id est laborum.</p>
    <p>Lorem ipsum dolor sit amet, consectetur adipisicing elit, sed do eiusmod tempor incididunt ut labore et dolore magna aliqua. Ut enim ad minim veniam, quis nostrud exercitation ullamco laboris nisi ut aliquip ex ea commodo consequat. Duis aute irure dolor in reprehenderit in voluptate velit esse cillum dolore eu fugiat nulla pariatur. Excepteur sint occaecat cupidatat non proident, sunt in culpa qui officia deserunt mollit anim id est laborum.</p>
    <p>Yours Sincerely,</p>
  </div>
  <div class="lh-signature" role="img" aria-label="Handwritten signature"></div>
  <span class="lh-mark"></span>
  <span class="accent-bar"></span>
  <div class="lh-footer"><p>42 طريق سيدار ريدج، فيرنون</p><p>كولومبيا البريطانية كندا V1T 5K8</p></div>
</article>

<article class="email-signature">
  <span class="sig-mark"></span>
  <p class="sig-name">KARIM DALTON <span class="ar">(كريم دالتون)</span></p>
  <p class="sig-title">Managing Director</p>
  <div class="sig-address-ar"><p>42 طريق سيدار ريدج، فيرنون</p><p>كولومبيا البريطانية كندا V1T 5K8</p></div>
  <ul class="sig-contacts">
    <li><svg class="icon" viewBox="0 0 16 16"><path d="M3 1h3l1.5 4-2 1.3a9 9 0 0 0 4.2 4.2L11 8.5l4 1.5v3a2 2 0 0 1-2 2A13 13 0 0 1 1 3a2 2 0 0 1 2-2z"/></svg>555.214.7720</li>
    <li><svg class="icon" viewBox="0 0 16 16"><path d="M1 3h14v10H1z M1 3l7 6 7-6" stroke="#fff" stroke-width="1.2"/></svg>info@northvanemail.com</li>
    <li><svg class="icon" viewBox="0 0 16 16"><circle cx="8" cy="8" r="7"/></svg>www.northvaneweb.com</li>
  </ul>
  <div class="sig-address-en"><p>42 Cedar Ridge Way, Vernon</p><p>B.C. Canada V1T 5K8</p></div>
</article>

</body>
</html>
```